New Wrestling company needs a website

We need a website design for a new wrestling company in Australia that will be running 3-4 events per year. Wrestling company is Summit Grip Wrestling (SGW).

The design of the logo is in place and can be provided, and I have purchased the website domain.

A detailed description of the intent and purpose of this company can be provided.

The aim would be to have around 5 specific pages on SGW, with two standard “about” and “contact” pages. E.g.
- About SGW (focus and purpose of the company)
- SGW Events (specific focus on events run by SGW)
- SGW News (news and stories on wrestling’s across Oceania)
- SGW Media (where to watch SGW and our partners))
- SGW Partners and Sponsors (partner and affiliate information)
- SGW Power Rankings (top 10 ranked wrestlers from Oceania which is updated weekly)
- SGW fans (highlighting how to become part of SGW as a fan)
- Contact SGW
Updates

The logo design should now be included in the brief, please feel free to reach out to me directly if you can't access it or require any other information.

Target Market(s)

Wrestling Fans

Industry/Entity Type

Sport / Wrestling

Coding

Coded - Design and coding required

Number of Pages Required

5+ page

Requirements
Must have
• A Wrestling and or Sports feel to the website design

```html
<!DOCTYPE html>
<html lang="en">
<head>
<meta charset="utf-8">
<title>Summit Grip Wrestling</title>
<link rel="stylesheet" href="https://fonts.googleapis.com/css2?family=Montserrat:wght@500;600;700&family=Open+Sans:wght@400;600&family=Abril+Fatface&display=swap">
<style>
:root{
  --blue:#1fa1e1;
  --blue-dark:#1a8fcb;
  --black:#000;
  --panel:#1d1d1d;
  --ink:#111;
  --white:#fff;
  --line:#555;
}
*{box-sizing:border-box;margin:0;padding:0}
html,body{width:1200px;height:4198px;overflow:hidden;background:var(--black)}
body{position:relative;font-family:"Open Sans",sans-serif;color:var(--white)}
.head{font-family:"Montserrat",sans-serif;font-weight:700;text-transform:uppercase}
.btn{position:absolute;display:inline-flex;align-items:center;justify-content:center;white-space:nowrap;background:var(--blue);color:var(--white);font-family:"Montserrat",sans-serif;font-weight:600;font-size:13px;letter-spacing:.2px;text-transform:uppercase;height:45px;padding:0 15px}
.btn.dark{background:var(--ink)}
.accent{color:var(--blue)}

/* hero */
.hero{position:absolute;left:0;top:0;width:1200px;height:785px;background:
  radial-gradient(ellipse 260px 120px at 50% 66%,#6a6a70 0%,rgba(60,60,66,.6) 50%,rgba(0,0,0,0) 100%),
  radial-gradient(ellipse 900px 420px at 50% 75%,#3a3836 0%,#1e1c1b 50%,rgba(0,0,0,0) 100%),
  linear-gradient(180deg,#050505 0%,#141416 35%,#23211f 70%,#0a0a0a 100%)}
.nav{position:absolute;top:64px;font-family:"Montserrat",sans-serif;font-weight:500;font-size:15px;display:flex;gap:28px}
.brand{position:absolute;left:490px;top:50px;width:220px;font-family:"Montserrat",sans-serif;font-weight:700;font-size:15px;line-height:1.3;display:flex;align-items:center;gap:8px;justify-content:center}
.brand .dot{width:30px;height:30px;border-radius:50%;background:var(--blue);flex:none}
.hero-title{position:absolute;left:0;width:1200px;text-align:center;font-family:"Montserrat",sans-serif;font-weight:700;text-transform:uppercase;line-height:1}
.hero-title.l1{top:275px;font-size:72px}
.hero-title.l2{top:355px;font-size:56px}

/* feature cards */
.card{position:absolute;top:792px;width:592px;height:268px;border:2px solid var(--blue-dark);background:#030303}
.card .photo{position:absolute;left:70px;top:10px;width:210px;height:254px;background:
  radial-gradient(ellipse 60px 90px at 50% 55%,#7a2a2a 0%,#3b2420 55%,rgba(3,3,3,0) 100%),
  radial-gradient(ellipse 110px 130px at 50% 50%,#2a2220 0%,#030303 100%)}
.card h3{position:absolute;left:350px;top:26px;font-family:"Montserrat",sans-serif;font-weight:500;font-size:32px}
.card p{position:absolute;left:350px;top:76px;width:210px;font-size:11.5px;line-height:21px}
.card .btn{left:350px;top:128px}

/* about */
.about{position:absolute;left:0;top:1068px;width:1200px;height:548px;background:var(--panel);border-bottom:2px solid var(--blue-dark)}
.about h2{position:absolute;left:173px;top:78px;font-size:30px}
.about .rule{position:absolute;left:173px;top:124px;width:72px;height:2px;background:var(--blue)}
.about .copy{position:absolute;left:173px;top:148px;width:448px;font-size:12px;line-height:22.5px;text-align:justify}
.about .copy p{margin-bottom:8px}
.about .btn{left:173px;top:438px}
.about .mark{position:absolute;left:690px;top:170px;width:400px;text-align:center;font-family:"Montserrat",sans-serif;font-weight:700;font-size:40px;line-height:1.25;color:#cfd6dc;text-transform:uppercase}
.about .mark .sq{display:block;width:110px;height:110px;border-radius:50%;background:var(--blue);margin:0 auto 24px}

/* rankings */
.rank{position:absolute;left:0;top:1616px;width:1200px;height:718px;background:radial-gradient(ellipse at 50% 30%,#2b2b2b 0%,#111 55%,#000 100%)}
.rank h2{position:absolute;left:0;top:84px;width:1200px;text-align:center;font-size:28px}
.rank .rule{position:absolute;left:527px;top:134px;width:146px;height:2px;background:var(--blue)}
.rank .figure{position:absolute;left:505px;top:205px;width:200px;height:513px;background:
  linear-gradient(180deg,rgba(0,0,0,0) 70%,#0a0a0a 100%),
  radial-gradient(ellipse 100px 260px at 50% 45%,#8a5a40 0%,#5a3a2a 55%,rgba(0,0,0,0) 100%)}
.entry{position:absolute;width:300px}
.entry h4{font-family:"Montserrat",sans-serif;font-weight:700;font-size:22px;text-transform:uppercase}
.entry p{font-size:12px;line-height:22px;margin-top:4px}
.entry.left{text-align:right}
.num{position:absolute;font-family:"Abril Fatface",serif;font-size:58px;line-height:1;color:var(--blue)}
.dots{position:absolute;height:0;border-top:1px dashed #888}
.arrow{position:absolute;top:405px}

/* partners */
.partners{position:absolute;left:0;top:2334px;width:1200px;height:728px;background:linear-gradient(180deg,#1b8ccc 0%,var(--blue) 40%,var(--blue) 100%)}
.partners h2{position:absolute;left:0;top:78px;width:1200px;text-align:center;font-size:28px}
.partners .intro{position:absolute;left:180px;top:156px;width:840px;text-align:center;font-size:13px;line-height:22px}
.pcol{position:absolute;top:240px;width:280px;text-align:center}
.pcol .photo{width:280px;height:202px;background:
  radial-gradient(ellipse 90px 70px at 50% 40%,#8a6a58 0%,rgba(0,0,0,0) 100%),
  linear-gradient(180deg,#3a3034 0%,#5a4a46 50%,#9a3232 100%)}
.pcol h3{font-family:"Montserrat",sans-serif;font-weight:600;font-size:17px;line-height:22px;margin-top:28px;text-transform:uppercase}
.pcol p{font-size:12px;line-height:22px;margin-top:10px;padding:0 6px}
.pcol .btn{position:static;margin-top:14px}

/* fans */
.fans{position:absolute;left:0;top:3062px;width:1200px;height:600px;background:var(--black)}
.fans .photo{position:absolute;left:0;top:0;width:620px;height:596px;background:
  radial-gradient(ellipse 140px 260px at 33% 50%,#7a5a48 0%,rgba(0,0,0,0) 100%),
  radial-gradient(ellipse 110px 220px at 58% 60%,#3a3232 0%,rgba(0,0,0,0) 100%),
  linear-gradient(90deg,#120e0c 0%,#050505 100%)}
.fans h2{position:absolute;left:636px;top:84px;font-size:30px}
.fans .copy{position:absolute;left:636px;top:168px;width:391px;font-size:12px;line-height:22.5px;text-align:justify}
.fans .btn{left:636px;top:468px}
.hr{position:absolute;left:173px;width:854px;height:1px;background:var(--line)}
.sponsors{position:absolute;left:173px;top:3680px;width:854px;height:88px;background:var(--white);display:flex;align-items:center;justify-content:space-around}
.sponsors span{display:block;width:96px;height:30px;background:#3a3a3a;border-radius:4px}
.sponsors span.round{width:46px;height:46px;border-radius:50%}

/* footer */
.fbrand{position:absolute;left:173px;top:3878px;font-family:"Montserrat",sans-serif;font-weight:700;font-size:22px;line-height:1.2;display:flex;gap:10px;align-items:center}
.fbrand .dot{width:34px;height:34px;border-radius:50%;background:var(--blue);flex:none}
.fdesc{position:absolute;left:173px;top:3983px;width:250px;font-size:12px;line-height:22px}
.fhead{position:absolute;top:3868px;font-family:"Montserrat",sans-serif;font-weight:600;font-size:16px}
.flinks{position:absolute;top:3898px;list-style:none;font-size:13px;line-height:23.5px}
.contact{position:absolute;left:794px;display:flex;gap:12px;align-items:flex-start;font-size:13px;line-height:20px}
.contact svg{flex:none}
.copyright{position:absolute;left:0;top:4148px;width:1200px;text-align:center;font-size:13px}
</style>
</head>
<body>

<header class="hero" role="img" aria-label="Packed arena with spotlights over a wrestling ring">
  <nav class="nav" style="left:171px"><span>HOME</span><span>ABOUT</span><span>EVENTS</span><span>NEWS</span></nav>
  <div class="brand"><span class="dot"></span><span>SUMMIT GRIP<br>WRESTLING</span></div>
  <nav class="nav" style="left:790px"><span>MEDIA</span><span>FAN</span><span>CONTACT US</span></nav>
  <h1 class="hero-title l1">Summit Grip</h1>
  <div class="hero-title l2">Wrestling</div>
  <a class="btn" style="left:539px;top:462px;height:50px;width:122px">Read More</a>
</header>

<article class="card" style="left:5px">
  <div class="photo" role="img" aria-label="Wrestler raising both arms to the crowd"></div>
  <h3>SGW Events</h3>
  <p>Duis aute irure dolor in reprehender it in voluptate velit</p>
  <a class="btn">Read More</a>
</article>
<article class="card" style="left:603px">
  <div class="photo" role="img" aria-label="Wrestler with arms spread wide"></div>
  <h3>SGW News</h3>
  <p>Duis aute irure dolor in reprehender it in voluptate velit</p>
  <a class="btn">Read More</a>
</article>

<section class="about">
  <h2 class="head">About <span class="accent">SGW</span></h2>
  <div class="rule"></div>
  <div class="copy">
    <p>Summit Grip Wrestling (SGW) has been created as a DESTINATION EVENT PRO WRESTLING company for OCEANIA. We want to collaborate with other wrestling companies (Oceania and International) in our event, media and fan outcomes.</p>
    <p>The creator and Managing Director of SGW is an experienced and successful Australian Sporting Administrator with 20 plus years' experience in sport as a CEO and COO in three major Australian sports, and a deep passion for the wrestling industry.</p>
    <p>At our core, SGW is a Wrestling Event Company to host events in Oceania that will attract International Talent AND International Wrestling Organizations in creating these unique, broadcast quality events while integrating Oceania talent and promotions where possible.</p>
  </div>
  <a class="btn">Read More</a>
  <div class="mark"><span class="sq"></span>Summit Grip<br>Wrestling</div>
</section>

<section class="rank">
  <h2 class="head"><span class="accent">SGW</span> Power Rankings</h2>
  <div class="rule"></div>
  <div class="figure" role="img" aria-label="Muscular wrestler standing in ring gear"></div>

  <svg class="arrow" style="left:66px" width="34" height="64" viewBox="0 0 34 64"><polyline points="32,2 2,32 32,62" fill="none" stroke="#fff" stroke-width="2"/></svg>
  <svg class="arrow" style="left:1098px" width="34" height="64" viewBox="0 0 34 64"><polyline points="2,2 32,32 2,62" fill="none" stroke="#fff" stroke-width="2"/></svg>

  <div class="entry left" style="left:70px;top:260px"><h4>Wrestler</h4><p>Nemo enim ipsam voluptatem quia<br>voluptas sit aspernatur aut</p></div>
  <div class="num" style="left:405px;top:260px">01</div>
  <div class="dots" style="left:173px;top:369px;width:300px"></div>
  <div class="entry left" style="left:70px;top:402px"><h4>Wrestler</h4><p>Nemo enim ipsam voluptatem quia<br>voluptas sit aspernatur aut</p></div>
  <div class="num" style="left:400px;top:402px">02</div>
  <div class="dots" style="left:173px;top:518px;width:300px"></div>
  <div class="entry left" style="left:70px;top:555px"><h4>Wrestler</h4><p>Nemo enim ipsam voluptatem quia<br>voluptas sit aspernatur aut</p></div>
  <div class="num" style="left:400px;top:555px">03</div>

  <div class="num" style="left:724px;top:260px">04</div>
  <div class="entry" style="left:830px;top:260px"><h4>Wrestler</h4><p>Nemo enim ipsam voluptatem quia<br>voluptas sit aspernatur aut</p></div>
  <div class="dots" style="left:727px;top:369px;width:300px"></div>
  <div class="num" style="left:724px;top:402px">05</div>
  <div class="entry" style="left:830px;top:402px"><h4>Wrestler</h4><p>Nemo enim ipsam voluptatem quia<br>voluptas sit aspernatur aut</p></div>
  <div class="dots" style="left:727px;top:518px;width:300px"></div>
  <div class="num" style="left:724px;top:555px">06</div>
  <div class="entry" style="left:830px;top:555px"><h4>Wrestler</h4><p>Nemo enim ipsam voluptatem quia<br>voluptas sit aspernatur aut</p></div>
</section>

<section class="partners">
  <h2 class="head">SGW Partners</h2>
  <p class="intro">To our partners, companies or wrestling talent, SGW is about OPPORTUNITY – wrestling or business. Wrestling partners will be from three key areas in our Event build.</p>
  <div class="pcol" style="left:173px">
    <div class="photo" role="img" aria-label="Wrestler leaping across the ring before a crowd"></div>
    <h3>International Wrestling Organisations</h3>
    <p>we will look to partner with as many International Wrestling Companies for mutually beneficial outcomes.</p>
    <a class="btn dark">Read More</a>
  </div>
  <div class="pcol" style="left:460px">
    <div class="photo" role="img" aria-label="Wrestler entering the ring among fans"></div>
    <h3>Australian Wrestling Companies</h3>
    <p>where possible we will elevate the talent and the promotions of the best Australian, NZ and other wrestling companies</p>
    <a class="btn dark">Read More</a>
  </div>
  <div class="pcol" style="left:747px">
    <div class="photo" role="img" aria-label="Two wrestlers grappling inside the ropes"></div>
    <h3>Free Agent Independent International Wrestlers</h3>
    <p>SGW events will be an opportunity for the strong base of international independent talent to appear as well.</p>
    <a class="btn dark">Read More</a>
  </div>
</section>

<section class="fans">
  <div class="photo" role="img" aria-label="Wrestler and manager walking toward the ring"></div>
  <h2 class="head"><span class="accent">SGW</span> Fans</h2>
  <div class="copy">
    The core business is SGW Events, with supporting SGW Media and touring SGW champions.<br>
    But the heartbeat of our events at SGW will be our SGW Fans – real fans of professional wrestling.<br>
    Our aim at SGW is to create a sense of belonging to professional wrestling fans in Oceania through membership and engagement like it does for other sports and clubs in Australia.<br>
    Membership in Australian sport is very important to create inclusion and belonging for people that love a sport or a sporting team. Wrestling fans in this region – Australia, NZ and the Islands LOVE professional wrestling, and we want to create that sense of belonging across all forms of pro wrestling in a simple membership model.
  </div>
  <a class="btn">Read More</a>
</section>

<div class="hr" style="top:3656px"></div>
<div class="sponsors" aria-label="Sponsor badges">
  <span></span><span></span><span class="round"></span><span></span><span class="round"></span><span></span>
</div>
<div class="hr" style="top:3798px"></div>

<footer>
  <div class="fbrand"><span class="dot"></span><span>SUMMIT GRIP<br>WRESTLING</span></div>
  <p class="fdesc">Nemo enim ipsam voluptatem quia voluptas sit aspernatur aut odit aut fugit, sed quia consequuntur magni dolores</p>

  <div class="fhead" style="left:460px">Quick Links</div>
  <ul class="flinks" style="left:460px"><li>Home</li><li>About</li><li>Events</li><li>News</li><li>Media</li><li>Fan</li><li>Contact Us</li></ul>
  <ul class="flinks" style="left:587px"><li>Partners and Sponsors</li><li>Power Rankings</li><li>SGW fans</li></ul>

  <div class="fhead" style="left:794px">Contact Us</div>
  <div class="contact" style="top:3904px">
    <svg width="30" height="30" viewBox="0 0 30 30"><circle cx="15" cy="15" r="15" fill="#1fa1e1"/><path d="M15 8a5 5 0 0 0-5 5c0 4 5 9 5 9s5-5 5-9a5 5 0 0 0-5-5z" fill="none" stroke="#fff" stroke-width="1.5"/><circle cx="15" cy="13" r="1.8" fill="#fff"/></svg>
    <span>48 Harbour Lane, Sydney,<br>NSW 2000</span>
  </div>
  <div class="contact" style="top:3964px">
    <svg width="30" height="30" viewBox="0 0 30 30"><circle cx="15" cy="15" r="15" fill="#1fa1e1"/><rect x="8" y="10" width="14" height="10" fill="none" stroke="#fff" stroke-width="1.5"/><polyline points="8,10 15,16 22,10" fill="none" stroke="#fff" stroke-width="1.5"/></svg>
    <span style="padding-top:5px">Email: hello@summitgrip.example</span>
  </div>
  <div class="contact" style="top:4016px">
    <svg width="30" height="30" viewBox="0 0 30 30"><circle cx="15" cy="15" r="15" fill="#1fa1e1"/><path d="M10 8l3 0 1.5 4-2 1.5a9 9 0 0 0 4 4l1.5-2 4 1.5 0 3a2 2 0 0 1-2 2A13 13 0 0 1 8 10a2 2 0 0 1 2-2z" fill="#fff"/></svg>
    <span style="padding-top:5px">Telephone: +61 (02)-555-0148</span>
  </div>

  <div class="hr" style="top:4120px"></div>
  <p class="copyright">Copyrights @ 2022 SGW. All Rights Reserved.</p>
</footer>

</body>
</html>
```